Website design for a hair building fibre

Hi I’m needing a website made for both men and women to purchase the product is a hair building fibre that you apply to thinning hair to make your hair look really thick I’ll need the website to be easy to use professional and also very classy I will need it to work with lumen split tok fund and credit cards I’ll need to have the CEO words and everything ready so I can sell I don’t have photos that I want to put on there so I’ll need a website designer to assist me in having the beautiful photos on there I know very little about websites so I need someone to be able to do it all for me

I can only provide photos of the colours of the products
I believe there will be 8 colours to sell as well
I’ve uploaded a photo of the logo I’d really like it if the website designer can check other competitors website so my website does not look like theres, I don’t want my website to look like a copied website of the competitors I’m located in Australia.
I’m also looking for someone who can open up a Palvista and Glimmerly page and then can unload photos on them ready for consumers to view and buy.

```html
<!DOCTYPE html>
<html lang="en">
<head>
<meta charset="utf-8">
<title>Millestrand – Hair Building Fibre</title>
<link href="https://fonts.googleapis.com/css2?family=Bebas+Neue&family=Roboto:wght@300;400;500;700&display=swap" rel="stylesheet">
<style>
:root{
  --navy:#1c2333;
  --navy-2:#242c3e;
  --sky:#7ec8e3;
  --sky-dark:#5fb3d3;
  --cream:#f7f3f0;
  --white:#ffffff;
  --text:#4a4a4a;
  --muted:#6b6b6b;
}
*{margin:0;padding:0;box-sizing:border-box}
html,body{width:1200px;height:3801px;overflow:hidden}
body{position:relative;font-family:'Roboto',sans-serif;background:var(--cream);color:var(--text)}
.abs{position:absolute}
.display{font-family:'Bebas Neue',sans-serif;font-weight:400;letter-spacing:1px}

/* header */
.site-header{left:0;top:0;width:1200px;height:102px;background:var(--navy)}
.brand{left:108px;top:28px;color:var(--sky);font-size:36px;font-weight:300;letter-spacing:2px}
.main-nav{left:385px;top:40px;display:flex;gap:36px;font-size:14px;font-weight:500;color:var(--white)}
.main-nav .active{color:var(--sky);border-bottom:2px solid var(--sky);padding-bottom:6px}
.call-box{left:917px;top:0;width:283px;height:102px;background:var(--sky);color:var(--white)}
.call-box small{position:absolute;left:102px;top:31px;font-size:13px}
.call-box strong{position:absolute;left:102px;top:50px;font-size:21px;font-weight:700}

/* hero */
.hero{left:0;top:102px;width:1200px;height:632px;overflow:hidden;background:linear-gradient(90deg,#3b3a3c 0%,#2a2729 40%,#1c1a22 70%,#2a2238 100%)}
.hero-photo{left:0;top:0;width:1200px;height:632px;background:radial-gradient(ellipse at 30% 40%,#a07d6a 0%,#5c4436 25%,rgba(40,34,36,0) 55%)}
.hero-title{left:674px;top:115px;font-size:72px;color:var(--white)}
.hero-text{left:677px;top:200px;width:420px;font-size:13px;line-height:26px;color:var(--white)}
.btn{background:var(--sky);color:var(--navy);font-size:13px;font-weight:700;text-align:center;box-shadow:0 3px 8px rgba(0,0,0,.2)}
.hero-btn{left:677px;top:274px;width:142px;height:46px;line-height:46px}
.hero-arrows{left:677px;top:376px;display:flex;gap:12px}
.hero-arrows span{width:32px;height:32px;border-radius:50%;background:#111;display:flex;align-items:center;justify-content:center}

/* about */
.about-frame{left:297px;top:791px;width:209px;height:191px;border:2px solid var(--sky);border-radius:8px}
.about-photo{left:109px;top:837px;width:354px;height:325px;border-radius:6px;background:linear-gradient(135deg,#4a5346,#2a2a2c 60%,#1a1a1c)}
.about-circle{left:366px;top:1006px;width:234px;height:234px;border-radius:50%;border:5px solid var(--white);background:radial-gradient(circle at 45% 40%,#c9a690,#8a6a58 60%,#3c3c40)}
.about-title{left:622px;top:820px;font-size:66px;color:var(--navy)}
.about-text{left:623px;top:913px;width:466px;font-size:13.5px;line-height:26px;text-align:justify;color:var(--muted)}
.about-text p+p{margin-top:26px}
.about-btn{left:623px;top:1188px;width:142px;height:46px;line-height:46px}

/* featured */
.featured-band{left:0;top:1339px;width:1200px;height:398px;background:linear-gradient(180deg,#8ccbe4,#79c0dc)}
.featured-title{left:0;top:1420px;width:1200px;text-align:center;font-size:72px;color:var(--white)}
.product-card{top:1531px;width:309px;height:369px;background:var(--white);box-shadow:0 4px 14px rgba(0,0,0,.08);text-align:center}
.product-img{position:absolute;left:104px;top:40px;width:100px;height:185px;border-radius:10px;background:linear-gradient(90deg,#8c8c8c,#f2f2f2 45%,#b8b8b8)}
.product-name{position:absolute;left:0;top:270px;width:100%;font-size:21px;font-weight:500;color:var(--navy)}
.product-price{position:absolute;left:0;top:316px;width:100%;font-size:20px;font-weight:500;color:var(--sky)}

/* colours */
.colour-panel{left:111px;top:1968px;width:977px;height:434px;background:var(--white);box-shadow:0 4px 14px rgba(0,0,0,.08)}
.colour-pointer{left:253px;top:1938px;width:0;height:0;border-left:16px solid transparent;border-right:16px solid transparent;border-bottom:30px solid var(--white)}
.colour-visual{left:111px;top:1968px;width:376px;height:434px;background:linear-gradient(160deg,#f3ede4,#eaeaea 50%,#dfe9d6)}
.swatch{width:104px;height:104px;border-radius:50%}
.swatch-label{width:170px;text-align:center;font-size:16px;font-weight:500;color:var(--navy)}

/* reviews */
.reviews-title{left:0;top:2484px;width:1200px;text-align:center;font-size:72px;color:var(--navy)}
.review-card{top:2622px;width:310px;height:327px;background:var(--navy);border-radius:4px;color:var(--white)}
.review-card p{position:absolute;left:35px;top:46px;width:246px;font-size:13px;line-height:26px}
.quote-mark{position:absolute;left:32px;top:-30px;font-family:'Bebas Neue',sans-serif;font-size:110px;line-height:1;color:var(--sky)}
.avatar{position:absolute;left:36px;top:238px;width:62px;height:62px;border-radius:50%;border:3px solid var(--sky);background:#b8a08e}
.reviewer{position:absolute;left:112px;top:242px}
.reviewer b{display:block;font-size:21px;font-weight:500}
.reviewer span{display:block;margin-top:8px;font-size:13px}
.review-arrow{top:2764px;width:48px;height:48px;border-radius:50%;background:var(--sky);display:flex;align-items:center;justify-content:center}

/* features */
.feature{top:3052px;width:260px;text-align:center}
.feature-icon{width:86px;height:86px;margin:0 auto;border-radius:50%;background:var(--navy);display:flex;align-items:center;justify-content:center}
.feature h4{margin-top:18px;font-size:16px;font-weight:700;color:var(--navy)}
.feature p{margin-top:12px;font-size:16px;color:var(--muted)}

/* footer */
.site-footer{left:0;top:3308px;width:1200px;height:493px;background:var(--navy);color:var(--white)}
.footer-brand{left:0;top:3380px;width:1200px;text-align:center;font-size:46px;font-weight:300;letter-spacing:3px;color:var(--sky)}
.footer-heading{top:3496px;font-size:25px}
.footer-text{font-size:13px;line-height:26px}
.newsletter{left:111px;top:3619px;width:373px;height:45px;display:flex;border:2px solid var(--white)}
.newsletter span{flex:1;background:var(--white);color:#777;font-size:13px;padding-left:16px;line-height:41px}
.newsletter b{width:130px;background:var(--sky);color:var(--navy);font-size:14px;text-align:center;line-height:41px}
.quick-links{left:590px;top:3557px;list-style:none;font-size:13px}
.quick-links li{line-height:26px}
.quick-links li::before{content:"»";margin-right:16px}
.social{left:796px;top:3641px;display:flex;gap:8px}
.social span{width:38px;height:38px;border-radius:50%;border:2px solid var(--white);display:flex;align-items:center;justify-content:center}
.social span i{width:8px;height:8px;border-radius:50%;background:var(--white)}
.copyright{left:0;top:3734px;width:1200px;text-align:center;font-size:13px}
</style>
</head>
<body>

<header class="abs site-header">
  <div class="abs brand">MILLESTRAND</div>
  <nav class="abs main-nav">
    <span class="active">Home</span><span>About us</span><span>Services</span><span>Blog</span><span>Contact</span>
    <svg width="14" height="14" viewBox="0 0 14 14"><circle cx="6" cy="6" r="4.5" fill="none" stroke="#fff" stroke-width="2"/><path d="M9 9l4 4" stroke="#fff" stroke-width="2"/></svg>
    <span>Login</span>
  </nav>
  <div class="abs call-box">
    <svg class="abs" style="left:48px;top:30px" width="46" height="42" viewBox="0 0 46 42"><path d="M8 4c3 0 6 6 6 8s-4 3-3 6 7 10 10 11 4-3 6-3 8 3 8 6-4 6-8 6C16 38 4 24 4 12c0-4 2-8 4-8z" fill="none" stroke="#fff" stroke-width="2.5"/><path d="M26 6a12 12 0 0 1 12 12M26 1a17 17 0 0 1 17 17" fill="none" stroke="#fff" stroke-width="2"/></svg>
    <small>Call us Today :</small>
    <strong>+1 555 010 0100</strong>
  </div>
</header>

<section class="abs hero">
  <div class="abs hero-photo" role="img" aria-label="Woman with long glossy straight brown hair"></div>
  <svg class="abs" style="left:70px;top:320px" width="690" height="320" viewBox="0 0 690 320"><path d="M10 312C40 190 140 80 280 55c160-28 290 40 390 150L690 320H0z" fill="#7ec8e3" opacity=".0"/><path d="M10 312C40 200 100 150 150 130L520 150c40 40 90 120 100 162z" fill="#7ec8e3"/></svg>
  <div class="abs" style="left:120px;top:0;width:640px;height:632px;background:radial-gradient(ellipse at 45% 45%,#6b5345 0%,#3e312c 40%,rgba(30,26,28,0) 70%)" role="img" aria-label="Hair model portrait"></div>
  <h1 class="abs display hero-title">Millestrand</h1>
  <p class="abs hero-text">Lorem ipsum dolor sit amet, consectetur adipiscing elit, sed do eiusmod tempor incididunt</p>
  <div class="abs btn hero-btn">SHOP NOW</div>
  <div class="abs hero-arrows">
    <span><svg width="10" height="12" viewBox="0 0 10 12"><path d="M7 1L2 6l5 5" fill="none" stroke="#fff" stroke-width="2"/></svg></span>
    <span><svg width="10" height="12" viewBox="0 0 10 12"><path d="M3 1l5 5-5 5" fill="none" stroke="#fff" stroke-width="2"/></svg></span>
  </div>
</section>

<section class="about">
  <div class="abs about-frame"></div>
  <div class="abs about-photo" role="img" aria-label="Bearded man in a barbershop"></div>
  <div class="abs about-circle" role="img" aria-label="Smiling woman combing wavy hair"></div>
  <h2 class="abs display about-title">About Us</h2>
  <div class="abs about-text">
    <p>Lorem ipsum dolor sit amet, consectetur adipiscing elit, sed do eiusmod tempor incididunt ut labore et dolore magna aliqua. Ut enim ad minim veniam, quis nostrud exercitation ullamco laboris nisi ut aliquip ex ea commodo consequat. Duis aute irure dolor in reprehenderit in voluptate velit esse cillum dolore eu fugiat nulla pariatur.</p>
    <p>Excepteur sint occaecat cupidatat non proident, sunt in culpa qui officia deserunt mollit anim id est laborum. Lorem ipsum dolor sit amet, consectetur adipiscing elit, sed do eiusmod tempor incididunt ut labore et dolore magna aliqua. Ut enim ad minim veniam</p>
  </div>
  <div class="abs btn about-btn">LEARN MORE →</div>
</section>

<section class="featured">
  <div class="abs featured-band"></div>
  <h2 class="abs display featured-title">Featured Product</h2>
  <article class="abs product-card" style="left:109px">
    <div class="product-img" role="img" aria-label="White fibre bottle with black cap"></div>
    <div class="product-name">Nemo enim ipsam</div><div class="product-price">$40.00</div>
  </article>
  <article class="abs product-card" style="left:444px">
    <div class="product-img" role="img" aria-label="Silver spray can"></div>
    <div class="product-name">Nemo enim ipsam</div><div class="product-price">$40.00</div>
  </article>
  <article class="abs product-card" style="left:779px">
    <div class="product-img" style="left:122px;width:64px;background:linear-gradient(90deg,#555,#aaa 45%,#666)" role="img" aria-label="Grey pump bottle"></div>
    <div class="product-name">Nemo enim ipsam</div><div class="product-price">$40.00</div>
  </article>

  <div class="abs colour-pointer"></div>
  <div class="abs colour-panel"></div>
  <div class="abs colour-visual" role="img" aria-label="Fibre bottle with brush, comb and palm leaves"></div>

  <div class="abs swatch" style="left:463px;top:2026px;background:radial-gradient(circle at 40% 35%,#6a3028,#3a1612)"></div>
  <div class="abs swatch" style="left:614px;top:2026px;background:radial-gradient(circle at 40% 35%,#6e5a30,#33280f)"></div>
  <div class="abs swatch" style="left:763px;top:2026px;background:radial-gradient(circle at 40% 35%,#a8792c,#5a3c10)"></div>
  <div class="abs swatch" style="left:912px;top:2026px;background:radial-gradient(circle at 40% 35%,#6a6a6a,#1e1e1e)"></div>
  <div class="abs swatch" style="left:463px;top:2200px;background:radial-gradient(circle at 40% 35%,#2a2a2a,#0e0e0e)"></div>
  <div class="abs swatch" style="left:614px;top:2200px;background:radial-gradient(circle at 40% 35%,#4a3430,#1e1210)"></div>
  <div class="abs swatch" style="left:763px;top:2200px;background:radial-gradient(circle at 40% 35%,#6a4e30,#2e2010)"></div>
  <div class="abs swatch" style="left:912px;top:2200px;background:radial-gradient(circle at 40% 35%,#5a2a22,#26100c)"></div>

  <div class="abs swatch-label" style="left:430px;top:2147px">Medium Brown</div>
  <div class="abs swatch-label" style="left:581px;top:2147px">Light Brown</div>
  <div class="abs swatch-label" style="left:730px;top:2147px">Light Blonde</div>
  <div class="abs swatch-label" style="left:879px;top:2147px">Gray</div>
  <div class="abs swatch-label" style="left:430px;top:2321px">Black</div>
  <div class="abs swatch-label" style="left:581px;top:2321px">Dark Brown</div>
  <div class="abs swatch-label" style="left:730px;top:2321px">Blonde</div>
  <div class="abs swatch-label" style="left:879px;top:2321px">Medium Blonde</div>
</section>

<section class="reviews">
  <h2 class="abs display reviews-title">Client Reviews</h2>
  <div class="abs review-arrow" style="left:32px"><svg width="20" height="16" viewBox="0 0 20 16"><path d="M18 8H3M9 2L3 8l6 6" fill="none" stroke="#fff" stroke-width="2.5"/></svg></div>
  <div class="abs review-arrow" style="left:1120px"><svg width="20" height="16" viewBox="0 0 20 16"><path d="M2 8h15M11 2l6 6-6 6" fill="none" stroke="#fff" stroke-width="2.5"/></svg></div>

  <article class="abs review-card" style="left:109px">
    <span class="quote-mark">“</span>
    <p>Lorem ipsum dolor sit amet, consectetur adipiscing elit, sed do eiusmod tempor incididunt ut labore et dolore magna aliqua. Ut enim ad minim veniam, quis nostrud exercitation ullamco laboris nisi ut aliquip ex ea commodo consequat.</p>
    <div class="avatar" role="img" aria-label="Client portrait"></div>
    <div class="reviewer"><b>John Doe</b><span>Company name</span></div>
  </article>
  <article class="abs review-card" style="left:444px">
    <span class="quote-mark">“</span>
    <p>Lorem ipsum dolor sit amet, consectetur adipiscing elit, sed do eiusmod tempor incididunt ut labore et dolore magna aliqua. Ut enim ad minim veniam, quis nostrud exercitation ullamco laboris nisi ut aliquip ex ea commodo consequat.</p>
    <div class="avatar" role="img" aria-label="Client portrait"></div>
    <div class="reviewer"><b>John Doe</b><span>Company name</span></div>
  </article>
  <article class="abs review-card" style="left:778px">
    <span class="quote-mark">“</span>
    <p>Lorem ipsum dolor sit amet, consectetur adipiscing elit, sed do eiusmod tempor incididunt ut labore et dolore magna aliqua. Ut enim ad minim veniam, quis nostrud exercitation ullamco laboris nisi ut aliquip ex ea commodo consequat.</p>
    <div class="avatar" role="img" aria-label="Client portrait"></div>
    <div class="reviewer"><b>John Doe</b><span>Company name</span></div>
  </article>
</section>

<section class="features">
  <div class="abs feature" style="left:71px">
    <div class="feature-icon"><svg width="46" height="34" viewBox="0 0 46 34" fill="none" stroke="#7ec8e3" stroke-width="2"><rect x="2" y="4" width="26" height="20"/><path d="M28 10h9l7 7v7H28z"/><circle cx="10" cy="28" r="4" fill="#1c2333"/><circle cx="36" cy="28" r="4" fill="#1c2333"/></svg></div>
    <h4>Free Delivery</h4><p>For all orders over $120</p>
  </div>
  <div class="abs feature" style="left:338px">
    <div class="feature-icon"><svg width="46" height="34" viewBox="0 0 46 34" fill="none" stroke="#7ec8e3" stroke-width="2"><rect x="2" y="6" width="34" height="24" rx="2"/><path d="M2 13h34M7 22h10"/><path d="M38 2l6 3v6c0 4-3 7-6 8-3-1-6-4-6-8V5z" fill="#1c2333"/></svg></div>
    <h4>Safe Payment</h4><p>100% secure payment</p>
  </div>
  <div class="abs feature" style="left:604px">
    <div class="feature-icon"><svg width="44" height="38" viewBox="0 0 44 38" fill="none" stroke="#7ec8e3" stroke-width="2"><path d="M4 2h36l3 10H1z"/><path d="M4 12v24h36V12M14 36V22h16v14"/></svg></div>
    <h4>Shop with Confidence</h4><p>Easy returns for you</p>
  </div>
  <div class="abs feature" style="left:871px">
    <div class="feature-icon"><svg width="44" height="44" viewBox="0 0 44 44" fill="none" stroke="#7ec8e3" stroke-width="2"><path d="M38 22A16 16 0 1 1 22 6"/><path d="M22 12v10l6 4"/><path d="M32 4l6 2-2 6"/></svg></div>
    <h4>24/7 Help Center</h4><p>Dedicated 24/7 Support</p>
  </div>
</section>

<footer class="abs site-footer"></footer>
<div class="abs footer-brand">MILLESTRAND</div>
<h3 class="abs display footer-heading" style="left:111px;color:#fff">Subscribe to Newsletter</h3>
<p class="abs footer-text" style="left:111px;top:3548px;width:380px;color:#fff">Lorem ipsum dolor sit amet, consectetur adipiscing elit sed do eiusmod tempor</p>
<div class="abs newsletter"><span>Email Address</span><b>SUBSCRIBE</b></div>
<h3 class="abs display footer-heading" style="left:590px;color:#fff">Quick Links</h3>
<ul class="abs quick-links" style="color:#fff"><li>History</li><li>Privacy Policy</li><li>Terms</li><li>Support</li><li>Contact</li></ul>
<h3 class="abs display footer-heading" style="left:796px;color:#fff">Connect With Us</h3>
<p class="abs footer-text" style="left:796px;top:3548px;width:300px;color:#fff">Lorem ipsum dolor sit amet, consectetur adipiscing elit, sed do eiusmod tempor incidid unt ut labore et dolore magna</p>
<div class="abs social">
  <span aria-label="Palvista"><i></i></span>
  <span aria-label="Chirpline"><i></i></span>
  <span aria-label="Glimmerly"><i></i></span>
  <span aria-label="Workloop"><i></i></span>
</div>
<p class="abs copyright" style="color:#fff">© Copyrights 2022 The Company Name.All Rights Reserved</p>

</body>
</html>
```